Business Cards - Brightpath Horizon

need to design unique business card for my mortgage business. I need to design credit card style business card for my business or any unique idea that you might have

Target Market(s)

Home Loan customers

Industry/Entity Type

Mortgage Brokerage

Contact Information for Business Card

please design credit card style or very unique style business card

Colors

Designer to choose colors to be used in the design.

Requirements
Must have
• Name
• position
• Phone number
• fax number
• email address
• website address
• social media address
• All above fields will be provided once design in finalised

```html
<!DOCTYPE html>
<html lang="en">
<head>
<meta charset="utf-8">
<title>Brightpath Horizon – Business Card</title>
<link rel="stylesheet" href="https://fonts.googleapis.com/css2?family=Old+Standard+TT:wght@400;700&family=Roboto:wght@400&display=swap">
<style>
  :root {
    --backdrop: #2a2a2a;
    --royal: #062fc0;
    --sky: #1fa6e6;
    --orange: #ff8c1a;
    --white: #ffffff;
    --serif: "Old Standard TT", Georgia, serif;
    --sans: "Roboto", Arial, sans-serif;
  }
  * { margin: 0; padding: 0; box-sizing: border-box; }
  html, body { width: 1200px; height: 960px; overflow: hidden; }
  body { background: var(--backdrop); position: relative; font-family: var(--serif); }

  .card {
    position: absolute;
    width: 600px;
    height: 343px;
    border-radius: 22px;
    overflow: hidden;
  }

  /* Front */
  .card--front { left: 314px; top: 113px; background: var(--white); }
  .front-band {
    position: absolute; left: 0; top: 212px; width: 100%; height: 131px;
    background: var(--royal);
  }
  .rooftop-art {
    position: absolute; left: 0; top: 212px; width: 268px; height: 131px;
  }
  .brand {
    position: absolute; line-height: 1;
    display: flex; flex-direction: column; align-items: flex-start;
  }
  .brand-name { font-size: 22px; letter-spacing: 1px; text-transform: uppercase; display: block; }
  .brand-name--large { font-size: 46px; letter-spacing: 0; line-height: 1; }
  .brand--front { left: 34px; top: 80px; color: var(--royal); }

  .holder {
    position: absolute; right: 35px; top: 82px; text-align: right;
  }
  .holder-name { color: var(--royal); font-size: 21px; font-weight: 700; line-height: 1.1; }
  .holder-role { color: var(--orange); font-size: 15px; margin-top: 3px; }

  .contacts {
    position: absolute; right: 36px; top: 239px; list-style: none;
    color: var(--white); font-size: 14px; text-align: right;
  }
  .contacts li { height: 19.3px; display: flex; justify-content: flex-end; align-items: center; gap: 7px; }
  .contacts svg { width: 13px; height: 13px; fill: var(--white); }

  /* Back */
  .card--back { left: 311px; top: 472px; background: var(--royal); }
  .socials {
    position: absolute; left: 33px; top: 47px; display: flex; gap: 3px; list-style: none;
  }
  .socials li { width: 26px; height: 26px; border-radius: 50%; background: var(--white); }
  .brand--back { left: 31px; top: 234px; color: var(--white); }
  .brand--back .brand-name { font-size: 24px; }
  .brand--back .brand-name--large { font-size: 46px; }
  .brand-url {
    display: block; font-family: var(--sans); font-size: 14px; letter-spacing: 3.5px; margin-top: 4px;
  }
  .tree-art {
    position: absolute; left: 262px; top: 0; width: 338px; height: 343px;
    background: radial-gradient(ellipse 60% 45% at 55% 40%, var(--sky) 0%, var(--sky) 70%, rgba(31,166,230,0) 100%);
  }
</style>
</head>
<body>

<section class="card card--front">
  <div class="brand brand--front">
    <span class="brand-name">Brightpath</span>
    <span class="brand-name brand-name--large">HORIZON</span>
  </div>

  <div class="holder">
    <h1 class="holder-name">DANIEL REYES</h1>
    <p class="holder-role">CEO/FOUNDER</p>
  </div>

  <div class="front-band"></div>
  <svg class="rooftop-art" role="img" aria-label="Illustration of house rooftops in orange and light blue" viewBox="0 0 268 131">
    <defs>
      <linearGradient id="roofTone" x1="0" y1="0" x2="1" y2="1">
        <stop offset="0" stop-color="#1fa6e6"/>
        <stop offset="0.45" stop-color="#ff8c1a"/>
        <stop offset="1" stop-color="#ff8c1a"/>
      </linearGradient>
    </defs>
    <polygon points="0,0 86,0 268,131 0,131" fill="url(#roofTone)"/>
  </svg>

  <ul class="contacts">
    <li>614 280 7395
      <svg viewBox="0 0 24 24"><path d="M6.6 10.8a15.1 15.1 0 0 0 6.6 6.6l2.2-2.2c.3-.3.7-.4 1-.2 1.1.4 2.3.6 3.6.6.6 0 1 .4 1 1V20c0 .6-.4 1-1 1C10.6 21 3 13.4 3 4c0-.6.4-1 1-1h3.5c.6 0 1 .4 1 1 0 1.3.2 2.5.6 3.6.1.3 0 .7-.2 1z"/></svg>
    </li>
    <li>614 280 7396
      <svg viewBox="0 0 24 24"><path d="M6 2h12v5H6zM3 9h18a2 2 0 0 1 2 2v7h-4v4H5v-4H1v-7a2 2 0 0 1 2-2zm4 8v3h10v-3z"/></svg>
    </li>
    <li>hello@brightpathhz.com
      <svg viewBox="0 0 24 24"><path d="M2 5h20v14H2zm2 2v.5l8 5 8-5V7l-8 5z"/></svg>
    </li>
    <li>www.brightpathhz.com
      <svg viewBox="0 0 24 24"><path d="M12 2a10 10 0 1 0 0 20 10 10 0 0 0 0-20zm6.9 9h-3a15 15 0 0 0-1.4-6A8 8 0 0 1 18.9 11zM12 4c.9 1.2 1.7 3.8 1.9 7h-3.8c.2-3.2 1-5.8 1.9-7zM9.5 5a15 15 0 0 0-1.4 6h-3A8 8 0 0 1 9.5 5zM5.1 13h3a15 15 0 0 0 1.4 6A8 8 0 0 1 5.1 13zM12 20c-.9-1.2-1.7-3.8-1.9-7h3.8c-.2 3.2-1 5.8-1.9 7zm2.5-1a15 15 0 0 0 1.4-6h3a8 8 0 0 1-4.4 6z"/></svg>
    </li>
  </ul>
</section>

<section class="card card--back">
  <ul class="socials" aria-label="Social media">
    <li></li><li></li><li></li><li></li>
  </ul>

  <div class="tree-art" role="img" aria-label="Large light blue tree silhouette"></div>

  <div class="brand brand--back">
    <span class="brand-name">Brightpath</span>
    <span class="brand-name brand-name--large">HORIZON</span>
    <span class="brand-url">www.brightpathhz.com</span>
  </div>
</section>

</body>
</html>
```